Business card for a new innovative and professional lawn care business

We need a business card design for a new lawn care business in Halifax NS Canada. We offer lawn services in Halifax & Bedford. Our services offered include lawn care, garden services, and property maintenance. We take pride in our work and are experienced at what we do. I would like to see a design that is double sided. On the backside I would like the something simple (maybe my logo preferably on blackround (linked below) with website link, Facebook page or something). The front I want to include contact info:
Morgan Pell
phone 902-555-0148
email - brookvaleyards.ca
facebook - townboard.com/brookvaleyards
Instagram maybe ? - picshare.com/brookvaleyard
Serving Halifax and Bedford for 5 years?
I don't want it to have too much information as I will be passing them out in aim to visit website, or call !
We do want it to include lawn care, garden services and property maintenance.
Basic, catchy, and modern looking !
Logo attached below !

Target Market(s)

Passing business cards to everyone I meet or interact with.

Industry/Entity Type

Lawn Care

Contact Information for Business Card

Double sided with some basic information, with catchy colours and easy to look at.

Font styles to use
Sans Serif

Requirements
Must have
• Must be double sided and have :
• Name, Phone, Email, FB, Website, and 3 main services offered - lawn care, property maintenance, garden services
Nice to have
• Would be nice to have instagram link if it goes well on there
Should not have
• Don't want too much writing or images that are distracting

```html
<!DOCTYPE html>
<html lang="en">
<head>
<meta charset="utf-8">
<title>Brookvale Yards – Business Card</title>
<link href="https://fonts.googleapis.com/css2?family=Open+Sans:wght@400;600;700;800&display=swap" rel="stylesheet">
<style>
  :root {
    --backdrop: #2a2a2a;
    --card-black: #050505;
    --card-white: #ffffff;
    --leaf: #8cc63f;
    --forest: #1f8f45;
    --ink-light: #f2f2f2;
  }
  * { box-sizing: border-box; margin: 0; padding: 0; }
  html, body {
    width: 1200px; height: 900px; overflow: hidden;
    background: var(--backdrop);
    font-family: "Open Sans", Arial, sans-serif;
  }
  .canvas { position: relative; width: 1200px; height: 900px; }
  .card {
    position: absolute; left: 250px;
    width: 700px; height: 400px;
    border-radius: 26px; overflow: hidden;
    background: var(--card-black);
    box-shadow: 0 14px 30px rgba(0,0,0,.45);
  }
  .card--back { top: 40px; }
  .card--front { top: 460px; }

  /* brand lockup */
  .brand {
    position: absolute; display: flex; align-items: center; gap: 12px;
    font-weight: 800; letter-spacing: 1px; text-transform: uppercase;
    white-space: nowrap;
  }
  .brand__dot { border-radius: 50%; flex: none; }
  .card--back .brand { left: 175px; top: 150px; font-size: 40px; color: var(--leaf); }
  .card--back .brand__dot { background: var(--leaf); width: 22px; height: 22px; }
  .card--front .brand { left: 40px; top: 178px; font-size: 26px; color: var(--forest); }
  .card--front .brand__dot { background: var(--forest); width: 16px; height: 16px; }

  /* social lines */
  .social {
    position: absolute; left: 34px; bottom: 34px;
    list-style: none; color: var(--ink-light); font-size: 17px; line-height: 30px;
  }
  .social li { display: flex; align-items: center; gap: 12px; }
  .social__mark { width: 14px; height: 14px; border-radius: 3px; background: var(--leaf); flex: none; }

  /* front layout */
  .front-art { position: absolute; inset: 0; }
  .details {
    position: absolute; right: 34px; top: 44px; text-align: right; color: var(--ink-light);
  }
  .details__name {
    color: var(--leaf); font-weight: 700; font-size: 30px; letter-spacing: .5px;
    text-transform: uppercase; line-height: 1.1; margin-bottom: 8px;
  }
  .contact, .services { list-style: none; }
  .contact li, .services li {
    display: flex; justify-content: flex-end; align-items: center; gap: 10px;
    font-size: 17px; line-height: 24px;
  }
  .contact svg { width: 14px; height: 14px; flex: none; }
  .services__title {
    color: var(--leaf); font-weight: 700; font-size: 22px; text-transform: uppercase;
    margin-top: 10px; line-height: 1.2;
  }
  .services li::after {
    content: ""; width: 8px; height: 8px; border-radius: 50%; background: var(--leaf); flex: none;
  }
</style>
</head>
<body>
<main class="canvas">

  <section class="card card--back" aria-label="Card back">
    <div class="brand"><span class="brand__dot"></span>Brookvale Yards</div>
    <ul class="social">
      <li><span class="social__mark"></span>townboard.com/brookvaleyards</li>
      <li><span class="social__mark"></span>picshare.com/brookvaleyard</li>
    </ul>
  </section>

  <section class="card card--front" aria-label="Card front">
    <svg class="front-art" viewBox="0 0 700 400" width="700" height="400" aria-hidden="true">
      <path d="M0 0 H250 A330 330 0 0 1 420 400 H0 Z" fill="var(--card-white)"/>
      <path d="M258 0 A330 330 0 0 1 430 400" fill="none" stroke="var(--leaf)" stroke-width="4"/>
    </svg>

    <div class="brand"><span class="brand__dot"></span>Brookvale Yards</div>

    <div class="details">
      <h1 class="details__name">Morgan Pell</h1>
      <ul class="contact">
        <li>902-555-0148
          <svg viewBox="0 0 16 16"><path d="M3 1l3 3-2 2c1 2 3 4 5 5l2-2 3 3-2 3C7 15 1 9 1 3z" fill="var(--leaf)"/></svg></li>
        <li>info@brookvaleyards.ca
          <svg viewBox="0 0 16 16"><rect x="1" y="3" width="14" height="10" rx="1" fill="none" stroke="var(--leaf)" stroke-width="1.6"/><path d="M1 4l7 5 7-5" fill="none" stroke="var(--leaf)" stroke-width="1.6"/></svg></li>
        <li>www.brookvaleyards.ca
          <svg viewBox="0 0 16 16"><circle cx="8" cy="8" r="6.5" fill="none" stroke="var(--leaf)" stroke-width="1.5"/><path d="M1.5 8h13M8 1.5c-3 3.5-3 9.5 0 13M8 1.5c3 3.5 3 9.5 0 13" fill="none" stroke="var(--leaf)" stroke-width="1.2"/></svg></li>
      </ul>
      <h2 class="services__title">Services</h2>
      <ul class="services">
        <li>Lawn care</li>
        <li>Garden services</li>
        <li>Property maintenance</li>
      </ul>
    </div>
  </section>

</main>
</body>
</html>
```